business card deign

Logo needs the following on it.
1. attached logo
2. Tagline - "If it keeps a drink cold or the party going...we do it!"
3. Name- Dalton Pikes, Founder and CPO
4. Address - 412 E. Carver Avenue, Ste 2207, Tampa, FL. 33917
5. Phone - 555.318.4726

```html
<!DOCTYPE html>
<html lang="en">
<head>
<meta charset="UTF-8">
<title>HOPLIN Business Card</title>
<link href="https://fonts.googleapis.com/css2?family=Montserrat:wght@400;500;700&display=swap" rel="stylesheet">
<style>
  :root {
    --backdrop: #1f1f1f;
    --card: #2b2b2b;
    --ink: #ffffff;
    --ink-soft: #d9d9d9;
    --rule: #8a8a8a;
  }
  * { box-sizing: border-box; margin: 0; padding: 0; }
  html, body {
    width: 1200px; height: 900px; overflow: hidden;
    background: var(--backdrop);
    font-family: "Montserrat", sans-serif;
    color: var(--ink);
  }
  .stage {
    width: 1200px; height: 900px;
    display: flex; flex-direction: column;
    align-items: center; justify-content: center; gap: 48px;
  }
  .card {
    width: 640px; height: 366px;
    background: var(--card);
    position: relative;
    box-shadow: 0 10px 24px rgba(0,0,0,.45);
  }
  .brand {
    display: flex; align-items: center; gap: 14px;
  }
  .brand-dot {
    width: 22px; height: 22px; border-radius: 50%;
    background: var(--ink);
  }
  .brand-name {
    font-weight: 700; font-size: 40px; letter-spacing: 12px;
    color: var(--ink);
  }
  /* front */
  .card-front .brand {
    position: absolute; left: 50%; top: 150px; transform: translateX(-50%);
  }
  .tagline {
    position: absolute; left: 0; right: 0; bottom: 34px;
    text-align: center; font-size: 13px; color: var(--ink-soft);
  }
  /* back */
  .card-back .brand {
    position: absolute; left: 70px; top: 160px;
  }
  .card-back .brand-name { font-size: 36px; letter-spacing: 10px; }
  .contact {
    position: absolute; left: 395px; top: 70px; bottom: 100px;
    border-left: 1px solid var(--rule);
    padding-left: 18px;
  }
  .contact-name { font-weight: 700; font-size: 20px; }
  .contact-role { font-size: 12px; color: var(--ink-soft); margin-top: 2px; }
  .contact-address { font-size: 12.5px; color: var(--ink-soft); margin-top: 22px; line-height: 1.35; }
  .contact-list { list-style: none; margin-top: 14px; }
  .contact-list li {
    display: flex; align-items: center; gap: 10px;
    font-size: 13px; color: var(--ink-soft); margin-bottom: 9px;
  }
  .contact-list svg { width: 13px; height: 13px; fill: var(--ink); flex: none; }
</style>
</head>
<body>
<main class="stage">
  <section class="card card-front">
    <div class="brand">
      <span class="brand-dot"></span>
      <span class="brand-name">HOPLIN</span>
    </div>
    <p class="tagline">If it keeps a drink cold or the party going...we do it</p>
  </section>

  <section class="card card-back">
    <div class="brand">
      <span class="brand-dot"></span>
      <span class="brand-name">HOPLIN</span>
    </div>
    <div class="contact">
      <h1 class="contact-name">Dalton Pikes</h1>
      <p class="contact-role">Founder and CPO</p>
      <p class="contact-address">412 E. Carver Avenue, Ste 2207,<br>Tampa, FL. 33917</p>
      <ul class="contact-list">
        <li>
          <svg viewBox="0 0 24 24" aria-hidden="true"><path d="M6.6 10.8a15.1 15.1 0 0 0 6.6 6.6l2.2-2.2a1 1 0 0 1 1-.25 11.4 11.4 0 0 0 3.6.57 1 1 0 0 1 1 1V20a1 1 0 0 1-1 1A17 17 0 0 1 3 4a1 1 0 0 1 1-1h3.5a1 1 0 0 1 1 1c0 1.25.2 2.45.57 3.6a1 1 0 0 1-.25 1z"/></svg>
          555.318.4726
        </li>
        <li>
          <svg viewBox="0 0 24 24" aria-hidden="true"><path d="M2 5h20v14H2z M2 5l10 8 10-8" fill="none" stroke="#fff" stroke-width="0"/><path d="M2 5h20v2l-10 7L2 7z"/><path d="M2 9l10 7 10-7v10H2z"/></svg>
          info@hoplin.com
        </li>
        <li>
          <svg viewBox="0 0 24 24" aria-hidden="true"><circle cx="12" cy="12" r="10"/><path d="M2 12h20M12 2c3 3 3 17 0 20M12 2c-3 3-3 17 0 20" stroke="#2b2b2b" stroke-width="1.5" fill="none"/></svg>
          www.hoplin.com
        </li>
      </ul>
    </div>
  </section>
</main>
</body>
</html>
```